R. Talmont Realty, Inc business card (2 sided), letterhead (1 sided) & #10 envelope (1 sided)

business card of standard size utilizing the attached logo. Side one with logo, Owen Talmont (my name), President / Broker (title), 805-317-2684 (phone), www.rtalmontrealty.example (website), 1726 Harlow Avenue, Suite 4052 San Luis Obiso, CA 93628 (business address) owen.rtalmontrealty@mailbox.example (e-mail address),
Side two - Log

Letterhead and #10 envelope in the same theme
Updates

Project Deadline Extended
Reason: I think a 2 day deadline may be a bit ambitious on my part. I have extended the deadline to 4 days. Thanks!

Industry/Entity Type

Business

```html
<!DOCTYPE html>
<html lang="en">
<head>
<meta charset="utf-8">
<title>R. Talmont Realty, Inc – Business Card</title>
<link rel="stylesheet" href="https://fonts.googleapis.com/css2?family=Open+Sans:wght@400;600&family=Roboto+Slab:wght@400;600&display=swap">
<style>
  :root {
    --page-bg: #ece8e1;
    --card-white: #ffffff;
    --brand-blue: #1b6f96;
    --brand-blue-light: #2a93c0;
    --brand-blue-deep: #0b4b6a;
    --ink-dark: #2e2e30;
    --ink-text: #333335;
    --rule-grey: #9a9a9a;
  }
  * { margin: 0; padding: 0; box-sizing: border-box; }
  html, body {
    width: 1200px; height: 1183px; overflow: hidden;
    background: var(--page-bg);
  }
  .card {
    position: absolute;
    border-radius: 32px;
    overflow: hidden;
    box-shadow: 0 4px 12px rgba(0,0,0,0.25);
  }
  /* Front */
  .card-front {
    left: 254px; top: 35px; width: 910px; height: 522px;
    background: var(--card-white);
  }
  .front-wordmark {
    position: absolute; left: 0; right: 0; top: 132px;
    text-align: center;
    font-family: "Roboto Slab", serif; font-weight: 400;
    font-size: 48px; color: var(--ink-dark);
    white-space: nowrap;
  }
  .holder {
    position: absolute; right: 524px; top: 300px; text-align: right;
    white-space: nowrap;
  }
  .holder-name {
    font-family: "Roboto Slab", serif; font-weight: 600;
    font-size: 32px; color: var(--brand-blue); line-height: 1.2;
  }
  .holder-title {
    font-family: "Roboto Slab", serif; font-weight: 400;
    font-size: 26px; color: var(--ink-text); margin-top: 8px; letter-spacing: 0.5px;
  }
  .divider {
    position: absolute; left: 409px; top: 280px; width: 1px; height: 113px;
    background: var(--rule-grey);
  }
  .contact-list {
    position: absolute; left: 428px; top: 280px; list-style: none;
    font-family: "Open Sans", sans-serif; font-size: 20px; color: var(--ink-text);
    white-space: nowrap;
  }
  .contact-list li { display: flex; align-items: center; height: 41px; }
  .contact-icon { width: 16px; height: 16px; margin-right: 8px; flex: none; }
  .front-swoosh { position: absolute; left: 0; top: 0; width: 910px; height: 522px; }
  /* Back */
  .card-back {
    left: 42px; top: 609px; width: 913px; height: 520px;
    background: radial-gradient(ellipse at 55% 50%, var(--brand-blue-light) 0%, var(--brand-blue) 45%, var(--brand-blue-deep) 100%);
  }
  .back-wordmark {
    position: absolute; left: 0; right: 0; top: 190px; text-align: center;
    font-family: "Roboto Slab", serif; font-weight: 400;
    font-size: 56px; color: #ffffff;
    white-space: nowrap;
  }
  .back-url {
    position: absolute; left: 0; right: 0; top: 420px; text-align: center;
    font-family: "Open Sans", sans-serif; font-weight: 600;
    font-size: 27px; letter-spacing: 3px; color: #ffffff;
    white-space: nowrap;
  }
</style>
</head>
<body>
  <section class="card card-front">
    <svg class="front-swoosh" viewBox="0 0 910 522" aria-hidden="true">
      <defs>
        <linearGradient id="swooshBlue" x1="0" x2="1" y1="0" y2="0">
          <stop offset="0" stop-color="#0f5577"/>
          <stop offset="0.5" stop-color="#2a93c0"/>
          <stop offset="1" stop-color="#0f5577"/>
        </linearGradient>
      </defs>
      <path d="M0 425 C 220 395, 460 405, 620 430 C 760 450, 850 420, 910 385 L910 522 L0 522 Z" fill="var(--ink-dark)"/>
      <path d="M0 455 C 220 430, 460 440, 630 462 C 770 478, 860 460, 910 440 L910 522 L0 522 Z" fill="#ffffff"/>
      <path d="M0 470 C 230 448, 470 458, 640 478 C 780 492, 860 478, 910 462 L910 522 L0 522 Z" fill="url(#swooshBlue)"/>
      <path d="M300 410 C 430 420, 540 440, 620 470 C 520 445, 410 428, 300 410 Z" fill="var(--ink-dark)"/>
    </svg>

    <div class="front-wordmark">R. Talmont Realty, Inc</div>

    <div class="holder">
      <div class="holder-name">Owen Talmont</div>
      <div class="holder-title">President / Broker</div>
    </div>

    <div class="divider"></div>

    <ul class="contact-list">
      <li>
        <svg class="contact-icon" viewBox="0 0 16 16" aria-hidden="true"><path d="M4 1.5 L6.5 4.5 L5 6 C6 8.3 7.7 10 10 11 L11.5 9.5 L14.5 12 L12.5 14.5 C7 13.5 2.5 9 1.5 3.5 Z" fill="none" stroke="var(--ink-text)" stroke-width="1.4"/></svg>
        805-317-2684
      </li>
      <li>
        <svg class="contact-icon" viewBox="0 0 16 16" aria-hidden="true"><circle cx="8" cy="8" r="7.5" fill="var(--brand-blue)"/><path d="M4 6 L8 9 L12 6 M4 6 H12 V11 H4 Z" fill="none" stroke="#fff" stroke-width="1.1"/></svg>
        owen.rtalmontrealty@mailbox.example
      </li>
      <li>
        <svg class="contact-icon" viewBox="0 0 16 16" aria-hidden="true"><circle cx="8" cy="8" r="7" fill="none" stroke="var(--brand-blue)" stroke-width="1.4"/><ellipse cx="8" cy="8" rx="3" ry="7" fill="none" stroke="var(--brand-blue)" stroke-width="1.1"/><path d="M1 8 H15" stroke="var(--brand-blue)" stroke-width="1.1"/></svg>
        www.rtalmontrealty.example
      </li>
    </ul>
  </section>

  <section class="card card-back">
    <div class="back-wordmark">R. Talmont Realty, Inc</div>
    <div class="back-url">www.rtalmontrealty.example</div>
  </section>
</body>
</html>
```